Oil Field Service company needs professional business cards

Looking to clean up our current company business cards and look a little more professional. Brenwick Casing Services is a US based company that services the oil field. We deal with engineers, managers and oil rigs....................................................................................................................................................................................................................................................................................................................................................................................................

Target Market(s)

Oil and Gas professionals

Industry/Entity Type

Oil And Gas

Contact Information for Business Card

See attached photo as example

Font styles to use
Sans Serif

Colors
ec1f27

Requirements
Must have
• Company Logo, Name, Title, Cell, Office, Fax, Email.
• See attached photo
Nice to have
• External CRT, Internal CRT, Casing Crews, Torque Turn, Laydown Machine
Should not have
• Do not introduce any new pictures and keep it professional looking

```html
<!DOCTYPE html>
<html lang="en">
<head>
<meta charset="utf-8">
<title>Brenwick Casing Services – Business Card</title>
<link rel="stylesheet" href="https://fonts.googleapis.com/css2?family=Oswald:wght@400;500&family=Roboto:wght@400;500&display=swap">
<style>
  :root {
    --page-bg: #e7e4df;
    --card-bg: #efeeeb;
    --panel-slate: #4b5968;
    --panel-slate-dark: #3f4b58;
    --brand-red: #ec1f27;
    --ink: #2f3338;
    --ink-soft: #3b3f44;
    --logo-ink: #e4e2df;
  }
  * { box-sizing: border-box; margin: 0; padding: 0; }
  html, body {
    width: 1200px; height: 1010px; overflow: hidden;
    background: var(--page-bg);
  }
  .business-card {
    position: absolute; left: 100px; top: 217px;
    width: 1000px; height: 575px;
    background: var(--card-bg);
    box-shadow: 0 10px 30px rgba(0,0,0,.18);
    overflow: hidden;
  }
  .brand-panel { position: absolute; inset: 0; width: 1000px; height: 575px; }
  .brand-name {
    position: absolute; left: 235px; top: 287px;
    transform: translate(-50%, -50%) rotate(-90deg);
    font-family: "Roboto", sans-serif; font-weight: 500;
    font-size: 38px; line-height: 1.25; letter-spacing: 4px;
    color: var(--logo-ink); text-align: center; white-space: nowrap;
    text-transform: uppercase;
  }
  .identity {
    position: absolute; right: 60px; top: 48px; text-align: right;
  }
  .identity .person-name {
    font-family: "Oswald", sans-serif; font-weight: 500;
    font-size: 44px; line-height: 1.1; color: var(--ink);
  }
  .identity .person-title {
    font-family: "Roboto", sans-serif; font-size: 21px;
    color: var(--ink-soft); margin-top: 4px;
  }
  .contact-list {
    position: absolute; right: 58px; top: 343px; list-style: none;
  }
  .contact-list li {
    display: flex; justify-content: flex-end; align-items: center;
    height: 32px;
    font-family: "Roboto", sans-serif; font-size: 21px; color: var(--ink-soft);
  }
  .contact-list .contact-icon {
    width: 20px; height: 20px; margin-left: 16px; flex: none;
    fill: var(--brand-red);
  }
</style>
</head>
<body>
  <div class="business-card">
    <svg class="brand-panel" viewBox="0 0 1000 575" aria-hidden="true">
      <defs>
        <linearGradient id="slate" x1="0" y1="0" x2="0" y2="1">
          <stop offset="0" stop-color="var(--panel-slate)"/>
          <stop offset="1" stop-color="var(--panel-slate-dark)"/>
        </linearGradient>
      </defs>
      <path d="M0 0 H378 C372 90 440 200 432 320 C425 430 370 520 345 575 H0 Z" fill="var(--brand-red)"/>
      <path d="M0 0 H366 C360 90 428 200 420 320 C413 430 358 520 332 575 H0 Z" fill="url(#slate)"/>
    </svg>

    <div class="brand-name">Brenwick<br>Casing Services</div>

    <div class="identity">
      <div class="person-name">Cody Marlowe</div>
      <div class="person-title">Area Manager</div>
    </div>

    <ul class="contact-list">
      <li>(555) 410-2870
        <svg class="contact-icon" viewBox="0 0 24 24"><path d="M6.6 10.8a15.1 15.1 0 0 0 6.6 6.6l2.2-2.2c.3-.3.7-.4 1-.2 1.1.4 2.3.6 3.6.6.6 0 1 .4 1 1V20c0 .6-.4 1-1 1A17 17 0 0 1 3 4c0-.6.4-1 1-1h3.5c.6 0 1 .4 1 1 0 1.3.2 2.5.6 3.6.1.3 0 .7-.2 1z"/></svg>
      </li>
      <li>(555) 618-3052
        <svg class="contact-icon" viewBox="0 0 24 24"><path d="M2 8c0-2 4-4 10-4s10 2 10 4v2h-5V8.5c-1.5-.5-3.3-.7-5-.7s-3.5.2-5 .7V10H2zm4 3h12l3 8H3z"/></svg>
      </li>
      <li>(555) 410-2914
        <svg class="contact-icon" viewBox="0 0 24 24"><path d="M6 2h12v5H6zM3 8h18a1 1 0 0 1 1 1v8h-4v5H6v-5H2V9a1 1 0 0 1 1-1zm5 7v5h8v-5z"/></svg>
      </li>
      <li>Harlan Springs, OK 73999
        <svg class="contact-icon" viewBox="0 0 24 24"><path d="M12 2a7 7 0 0 0-7 7c0 5 7 13 7 13s7-8 7-13a7 7 0 0 0-7-7zm0 9.5A2.5 2.5 0 1 1 12 6.5a2.5 2.5 0 0 1 0 5z"/></svg>
      </li>
      <li>codymarlowe@brenwicksrvs.com
        <svg class="contact-icon" viewBox="0 0 24 24"><path d="M2 5h20v14H2zm2 2v.5l8 5.5 8-5.5V7l-8 5z"/></svg>
      </li>
      <li>www.brenwicksrvs.com
        <svg class="contact-icon" viewBox="0 0 24 24"><path d="M12 2a10 10 0 1 0 0 20 10 10 0 0 0 0-20zm6.9 6h-2.9a15 15 0 0 0-1.4-3.6A8 8 0 0 1 18.9 8zM12 4c.8 1.2 1.5 2.5 1.9 4h-3.8c.4-1.5 1.1-2.8 1.9-4zM4.3 14a8 8 0 0 1 0-4h3.4a16 16 0 0 0 0 4zm.8 2h2.9c.3 1.3.8 2.5 1.4 3.6A8 8 0 0 1 5.1 16zM8 8H5.1a8 8 0 0 1 4.3-3.6C8.8 5.5 8.3 6.7 8 8zm4 12c-.8-1.2-1.5-2.5-1.9-4h3.8c-.4 1.5-1.1 2.8-1.9 4zm2.3-6H9.7a14 14 0 0 1 0-4h4.6a14 14 0 0 1 0 4zm.3 5.6c.6-1.1 1.1-2.3 1.4-3.6h2.9a8 8 0 0 1-4.3 3.6zm1.7-5.6a16 16 0 0 0 0-4h3.4a8 8 0 0 1 0 4z"/></svg>
      </li>
    </ul>
  </div>
</body>
</html>
```